Personal Training Business at home (Fern Vitality & Health)

My business name will be Fern Vitality & Health and will be training people with special needs (Asthma, Diabetes, Obesity, Rehab, Sports Performance) for all ages. It will be set indoor and outdoor for all types of weather conditions. I,m also doing Pilates group classes as well in a Japanese garden setting.I will be working alone so the groups will be small and the client has a high quality of service. I just need something very basic to start with then as the business expands I can edit it to it,s growth.

Target Market(s)

Target special population persons with dysfunctions injuries, metabolic/cardio-respiratory conditions, sports performance and more also healthy food choices.

Industry/Entity Type

Business

Number of Pages Required

3 page

Font styles to use
Serif

Colors
f78f20
ffffff
474747
cbcbcb
abd036

Requirements
Must have
• The website must have accessibility for change, to be able to link on other networks like my own YouTube videos. A basic lay out so I can fill in the pages and ad more as I expand the business. The logo to have the A for Fern to be an image of a man shaped as the letter A with his arms extended out/up. Private Facility and must ring for appointment to enter premises.
Nice to have
• The Image I want to have in my studio is for people to be serious about training & health choices. I want them to be able to train in a comfortable environment and free of air conditioned concrete rooms with machines. My home is converted to a Organic feature and outdoor/indoor training facility that my clients & I can share the natural freedom of training in the elements. My client have special needs and need extra care, they are people with injuries, metabolic/cardio-respiratory condition, asthmatics & more they need to be screened and tested for the condition that they suffer from and together with there allied professional we work together to treat them with the up most care for maximum results. This is what I want to target I long term client with real Goals on there mind and not some pipe dream.
Should not have
• Not to be portray as a Gym with machines and clients that only care about image.

```html
<!DOCTYPE html>
<html lang="en">
<head>
<meta charset="utf-8">
<title>Fern Vitality & Health</title>
<link href="https://fonts.googleapis.com/css2?family=Oswald:wght@400;500&family=Open+Sans:wght@400;600&display=swap" rel="stylesheet">
<style>
:root{
  --orange:#f78f20;
  --green:#abd036;
  --dark:#474747;
  --darker:#2b2b2b;
  --night:#1f1f1f;
  --grey:#cbcbcb;
  --white:#ffffff;
  --text:#5a5a5a;
}
*{margin:0;padding:0;box-sizing:border-box}
html,body{width:1200px;height:2572px;overflow:hidden;background:var(--white)}
body{font-family:"Open Sans",sans-serif;color:var(--text);font-size:14px;position:relative}
.heading{font-family:"Oswald",sans-serif;font-weight:400;text-transform:uppercase;letter-spacing:1px}
section,header,footer{position:absolute;left:0;width:1200px}

.topbar{top:0;height:32px;background:var(--white);border-bottom:1px solid #eee;font-size:12px;color:#888}
.topbar .contact{position:absolute;right:40px;top:8px;display:flex;gap:30px}
.navbar{top:32px;height:108px;background:var(--white)}
.brand{position:absolute;left:40px;top:30px;display:flex;align-items:center;gap:12px}
.brand-mark{width:40px;height:40px;border-radius:50%;background:var(--orange)}
.brand-name{font-family:"Oswald",sans-serif;font-size:26px;color:var(--dark);text-transform:uppercase;letter-spacing:1px}
.menu{position:absolute;right:40px;top:30px;display:flex;gap:2px}
.menu a{display:block;padding:14px 22px;font-family:"Oswald",sans-serif;font-size:15px;text-transform:uppercase;color:var(--dark);text-decoration:none}
.menu a.active{background:var(--green);color:var(--white)}

.hero{top:140px;height:470px}
.hero-photo{position:absolute;inset:0;background:linear-gradient(135deg,#3f5a2a 0%,#6d8a3e 35%,#2c3a22 60%,#5b6f34 100%)}
.hero-caption{position:absolute;left:0;right:0;top:250px;text-align:center}
.hero-caption .kicker{font-family:"Oswald",sans-serif;font-size:28px;color:var(--green);text-transform:uppercase}
.hero-caption .tagline{display:inline-block;margin-top:10px;padding:12px 30px;background:rgba(0,0,0,.65);color:var(--white);font-family:"Oswald",sans-serif;font-size:30px;text-transform:uppercase;letter-spacing:1px}

.welcome{top:610px;height:270px;text-align:center}
.welcome h2{margin-top:50px;font-size:24px;color:var(--dark)}
.welcome p{width:900px;margin:16px auto 0;font-size:13px;line-height:20px}
.enquiry{margin-top:26px;display:flex;justify-content:center;align-items:center;gap:20px;font-size:16px;color:var(--dark)}
.phone-btn{background:var(--orange);color:var(--white);padding:10px 26px;border-radius:3px;font-weight:600;display:flex;align-items:center;gap:8px}

.services{top:880px;height:460px;background:linear-gradient(180deg,#e6e6e6,#d4d4d4);text-align:center}
.services h2{margin-top:34px;font-size:24px;color:var(--dark)}
.services .intro{width:900px;margin:14px auto 0;font-size:12px;line-height:18px}
.service-grid{display:grid;grid-template-columns:repeat(4,220px);justify-content:center;column-gap:50px;row-gap:20px;margin-top:30px}
.service{display:flex;flex-direction:column;align-items:center;gap:10px}
.service span{font-family:"Oswald",sans-serif;font-size:13px;text-transform:uppercase;color:var(--dark)}
.service .hex{fill:var(--dark);stroke:#5c5c5c;stroke-width:2}
.service .ico{fill:none;stroke:var(--white);stroke-width:4;stroke-linecap:round;stroke-linejoin:round}
.service .ico-fill{fill:var(--white)}

.why{top:1340px;height:590px;background:linear-gradient(180deg,#2d2d2d,#3a3a3a);text-align:center}
.why h2{margin-top:36px;font-size:24px;color:var(--white)}
.why p{width:960px;margin:14px auto 0;font-size:12px;line-height:18px;color:var(--grey)}
.video{position:absolute;left:140px;top:140px;width:920px;height:410px;background:linear-gradient(135deg,#2f3b26,#6a7a44 50%,#3a4a2c);}
.video-bar{position:absolute;left:0;right:0;bottom:0;height:36px;background:rgba(0,0,0,.75)}
.video-bar .track{position:absolute;left:90px;right:150px;top:16px;height:4px;background:#666}
.play{position:absolute;left:50%;top:50%;transform:translate(-50%,-50%)}

.blog{top:1930px;height:390px;text-align:center}
.blog-head{display:flex;justify-content:center;align-items:center;gap:30px;margin-top:40px}
.blog-head h2{font-size:24px;color:var(--dark)}
.arrow{width:32px;height:32px;border:1px solid var(--grey);border-radius:50%;display:flex;align-items:center;justify-content:center}
.posts{display:flex;justify-content:center;gap:80px;margin-top:36px;text-align:left}
.post{display:flex;gap:20px;width:480px}
.post-photo{width:200px;height:160px;flex:none;background:linear-gradient(135deg,#7b9a45,#c8b56a)}
.post h3{font-family:"Oswald",sans-serif;font-weight:400;font-size:17px;color:var(--dark)}
.post .date{font-size:11px;color:#999;margin:6px 0}
.post p{font-size:12px;line-height:18px}
.post .more{display:inline-block;margin-top:8px;color:var(--orange);font-size:12px;font-weight:600}

.footer{top:2320px;height:220px;background:var(--night);color:var(--grey)}
.footer .col{position:absolute;top:30px}
.footer h4{font-family:"Oswald",sans-serif;font-weight:400;font-size:18px;color:var(--white);text-transform:uppercase;margin-bottom:18px}
.footer h4 b{color:var(--orange);font-weight:400}
.signup{left:40px;width:330px}
.signup form{display:flex}
.signup .field{flex:1;height:34px;background:var(--white)}
.signup .btn{background:var(--orange);color:var(--white);padding:8px 16px;font-size:12px;font-weight:600}
.signup p{font-size:11px;line-height:17px;margin-top:14px}
.hours{left:420px;width:500px}
.hours .cols{display:flex;gap:50px}
.hours .season{font-family:"Oswald",sans-serif;color:var(--white);font-size:14px;margin-bottom:8px}
.hours ul{list-style:none}
.hours li{font-size:11px;line-height:20px;border-bottom:1px solid #333}
.contact-col{left:970px;width:200px;font-size:11px;line-height:20px}
.contact-col li{list-style:none;display:flex;gap:8px;align-items:center}
.copyright{top:2540px;height:32px;background:#141414;color:#888;font-size:11px;padding:9px 40px}
</style>
</head>
<body>

<header class="topbar">
  <div class="contact"><span>0400 123 456</span><span>hello@fernvitality.example</span></div>
</header>

<header class="navbar">
  <div class="brand"><span class="brand-mark"></span><span class="brand-name">Fern Fitness</span></div>
  <nav class="menu">
    <a class="active">Home</a><a>About Us</a><a>Our Services</a><a>Why Fern Fitness</a><a>Pricing</a><a>Blog</a><a>Contact</a>
  </nav>
</header>

<section class="hero">
  <div class="hero-photo" role="img" aria-label="Woman stretching on a mat in a lush Japanese garden"></div>
  <div class="hero-caption">
    <div class="kicker">Fern Fitness</div>
    <div class="tagline">We are a personal training &amp; fitness company from home</div>
  </div>
</section>

<section class="welcome">
  <h2 class="heading">Welcome to Fern Fitness</h2>
  <p>Fern Vitality &amp; Health offers personal training in a calm home studio and garden setting. We work with special populations including asthma, diabetes, obesity, rehab and sports performance clients of all ages. Every client is screened and supported with care alongside their allied health professionals for lasting, real results.</p>
  <div class="enquiry">
    <span>For enquiries &amp; Bookings ring Marcus on</span>
    <span class="phone-btn">
      <svg width="14" height="14" viewBox="0 0 24 24"><path fill="#fff" d="M6.6 10.8a15 15 0 0 0 6.6 6.6l2.2-2.2a1 1 0 0 1 1-.25 11.4 11.4 0 0 0 3.6.6 1 1 0 0 1 1 1V20a1 1 0 0 1-1 1A17 17 0 0 1 3 4a1 1 0 0 1 1-1h3.5a1 1 0 0 1 1 1c0 1.25.2 2.45.6 3.6a1 1 0 0 1-.25 1z"/></svg>
      0400 123 456
    </span>
  </div>
</section>

<section class="services">
  <h2 class="heading">Our Services</h2>
  <p class="intro">Our sessions are tailored to each person, indoors or outdoors in any weather. Small groups and private training mean every client receives focused attention and a program built around their needs.</p>
  <div class="service-grid">
    <div class="service">
      <svg width="86" height="96" viewBox="0 0 86 96"><polygon class="hex" points="43,2 84,25 84,71 43,94 2,71 2,25"/>
        <g class="ico"><line x1="26" y1="48" x2="60" y2="48"/><line x1="26" y1="38" x2="26" y2="58"/><line x1="60" y1="38" x2="60" y2="58"/><line x1="20" y1="42" x2="20" y2="54"/><line x1="66" y1="42" x2="66" y2="54"/></g></svg>
      <span>Personal Training and Rehab</span></div>
    <div class="service">
      <svg width="86" height="96" viewBox="0 0 86 96"><polygon class="hex" points="43,2 84,25 84,71 43,94 2,71 2,25"/>
        <g class="ico-fill"><circle cx="43" cy="36" r="7"/><circle cx="29" cy="58" r="7"/><circle cx="57" cy="58" r="7"/></g></svg>
      <span>Group Functional Training</span></div>
    <div class="service">
      <svg width="86" height="96" viewBox="0 0 86 96"><polygon class="hex" points="43,2 84,25 84,71 43,94 2,71 2,25"/>
        <g class="ico"><circle cx="43" cy="52" r="15"/><line x1="43" y1="52" x2="43" y2="43"/><line x1="43" y1="52" x2="50" y2="56"/><line x1="38" y1="31" x2="48" y2="31"/></g></svg>
      <span>Sports Performance</span></div>
    <div class="service">
      <svg width="86" height="96" viewBox="0 0 86 96"><polygon class="hex" points="43,2 84,25 84,71 43,94 2,71 2,25"/>
        <g class="ico"><path d="M59 44 A17 17 0 0 0 28 40"/><polyline points="28,31 28,40 37,40"/><path d="M27 52 A17 17 0 0 0 58 56"/><polyline points="58,65 58,56 49,56"/></g></svg>
      <span>Recovery &amp; Stretching Classes</span></div>
    <div class="service">
      <svg width="86" height="96" viewBox="0 0 86 96"><polygon class="hex" points="43,2 84,25 84,71 43,94 2,71 2,25"/>
        <g class="ico"><rect x="22" y="52" width="42" height="8" rx="2"/><circle cx="43" cy="38" r="6"/></g></svg>
      <span>Pilates</span></div>
    <div class="service">
      <svg width="86" height="96" viewBox="0 0 86 96"><polygon class="hex" points="43,2 84,25 84,71 43,94 2,71 2,25"/>
        <g class="ico"><rect x="24" y="32" width="38" height="32" rx="5"/><path d="M33 44 A10 10 0 0 1 53 44"/><line x1="43" y1="44" x2="47" y2="38"/></g></svg>
      <span>Weight Loss Programs</span></div>
    <div class="service">
      <svg width="86" height="96" viewBox="0 0 86 96"><polygon class="hex" points="43,2 84,25 84,71 43,94 2,71 2,25"/>
        <g class="ico"><line x1="33" y1="30" x2="33" y2="66"/><line x1="27" y1="30" x2="27" y2="40"/><line x1="39" y1="30" x2="39" y2="40"/><path d="M27 40 Q33 46 39 40"/><path d="M54 66 V30 Q62 38 60 50 H54"/></g></svg>
      <span>Nutrition &amp; Healthy Food</span></div>
    <div class="service">
      <svg width="86" height="96" viewBox="0 0 86 96"><polygon class="hex" points="43,2 84,25 84,71 43,94 2,71 2,25"/>
        <path class="ico-fill" d="M43 66 L28 51 a9 9 0 0 1 15-11 a9 9 0 0 1 15 11 z"/></svg>
      <span>Basic Lifestyle Conditioning</span></div>
  </div>
</section>

<section class="why">
  <h2 class="heading">Why train with us</h2>
  <p>Our training sessions cover a wide variety of needs, from injuries and metabolic conditions to asthma and sports goals. Clients train in a natural, open environment away from machines and concrete rooms, with extra care for anyone needing supervision, screening and close cooperation with their health team.</p>
  <div class="video" role="img" aria-label="Video of the garden training space with bonsai trees">
    <svg class="play" width="80" height="80" viewBox="0 0 80 80"><circle cx="40" cy="40" r="38" fill="rgba(0,0,0,.5)" stroke="#fff" stroke-width="2"/><polygon points="32,24 58,40 32,56" fill="#fff"/></svg>
    <div class="video-bar"><div class="track"></div></div>
  </div>
</section>

<section class="blog">
  <div class="blog-head">
    <span class="arrow"><svg width="10" height="14" viewBox="0 0 10 14"><path d="M8 1 L2 7 L8 13" stroke="#474747" stroke-width="2" fill="none"/></svg></span>
    <h2 class="heading">Latest Blog</h2>
    <span class="arrow"><svg width="10" height="14" viewBox="0 0 10 14"><path d="M2 1 L8 7 L2 13" stroke="#474747" stroke-width="2" fill="none"/></svg></span>
  </div>
  <div class="posts">
    <article class="post">
      <div class="post-photo" role="img" aria-label="Outdoor group stretching on grass"></div>
      <div>
        <h3>NEW PRICES for Lakeside Garden Studio</h3>
        <div class="date">26 February 2024 · News</div>
        <p>New session prices for the Lakeside garden studio start this month. Small group places are limited, so book early to secure your preferred weekly time slot.</p>
        <span class="more">Read More</span>
      </div>
    </article>
    <article class="post">
      <div class="post-photo" role="img" aria-label="Pilates class in a garden"></div>
      <div>
        <h3>NEW PRICES for Lakeside Garden Studio</h3>
        <div class="date">26 February 2024 · News</div>
        <p>Garden Pilates classes return with updated pricing and extra morning sessions. Contact us to discuss which class suits your needs and current fitness level.</p>
        <span class="more">Read More</span>
      </div>
    </article>
  </div>
</section>

<footer class="footer">
  <div class="col signup">
    <h4>Sign up our <b>newsletter!</b></h4>
    <form><div class="field"></div><div class="btn">Submit</div></form>
    <p>Receive training tips, healthy food ideas and studio news straight to your inbox each month.</p>
  </div>
  <div class="col hours">
    <h4>Training <b>hours</b></h4>
    <div class="cols">
      <div>
        <div class="season">April – September</div>
        <ul>
          <li>Monday – Friday: 6.00am – 7.00pm</li>
          <li>Saturday: 7.00am – 12.00pm</li>
          <li>Sunday: Closed</li>
        </ul>
      </div>
      <div>
        <div class="season">October – March</div>
        <ul>
          <li>Monday – Friday: 5.30am – 7.30pm</li>
          <li>Saturday: 6.30am – 12.00pm</li>
          <li>Sunday: Closed</li>
        </ul>
      </div>
    </div>
  </div>
  <div class="col contact-col">
    <h4>Contact <b>us</b></h4>
    <ul>
      <li><svg width="12" height="14" viewBox="0 0 12 16"><path d="M6 0a6 6 0 0 1 6 6c0 4.5-6 10-6 10S0 10.5 0 6a6 6 0 0 1 6-6z" fill="#f78f20"/><circle cx="6" cy="6" r="2" fill="#1f1f1f"/></svg>12 Garden Lane, Greenvale</li>
      <li><svg width="12" height="12" viewBox="0 0 24 24"><path fill="#f78f20" d="M6.6 10.8a15 15 0 0 0 6.6 6.6l2.2-2.2a1 1 0 0 1 1-.25 11.4 11.4 0 0 0 3.6.6 1 1 0 0 1 1 1V20a1 1 0 0 1-1 1A17 17 0 0 1 3 4a1 1 0 0 1 1-1h3.5a1 1 0 0 1 1 1c0 1.25.2 2.45.6 3.6a1 1 0 0 1-.25 1z"/></svg>0400 123 456</li>
      <li><svg width="12" height="10" viewBox="0 0 16 12"><rect width="16" height="12" fill="#f78f20"/><path d="M0 0 L8 7 L16 0" stroke="#1f1f1f" fill="none"/></svg>hello@fernvitality.example</li>
    </ul>
  </div>
</footer>
<footer class="copyright">Copyright © 2024 Fern Fitness. All Rights Reserved</footer>

</body>
</html>
```